Vehicle Rental Hire in the Valmora Coast

We are opening a Vehicle Rental company in the Valmora Coast - this will attract both locals and Tourists visiting. So we want this website to capture the beautiful location we will be set in, along with the familiarity of a vehicle rental company. And to keep a colour scheme in Line with out Logo. We are Quenmira Vehicle Rental.

Industry/Entity Type

Vehicle Rental

Number of Pages Required

1 page

Requirements
Must have
• must be professional, and simple to use navigation bar - must also have a "make a reservation" box - similar to the screenshot attached - Under our logo it must read "Vehicle Rental"
Nice to have
• It needs to be in a colour scheme that fits in with our logo

```html
<!DOCTYPE html>
<html lang="en">
<head>
<meta charset="utf-8">
<title>Quenmira Vehicle Rental</title>
<link href="https://fonts.googleapis.com/css2?family=Montserrat:wght@400;500;600;700;800&display=swap" rel="stylesheet">
<style>
:root{
  --blue:#1a0fd6;
  --red:#c7322b;
  --ink:#222;
  --muted:#555;
  --dark:#111;
  --light:#f3f3f5;
  --line:#c94a44;
}
*{box-sizing:border-box;margin:0;padding:0}
html,body{width:1200px;height:3059px;overflow:hidden}
body{font-family:'Montserrat',sans-serif;color:var(--ink);background:#fff;position:relative}
.topbar{height:38px;background:var(--blue);color:#fff;font-size:14px;font-weight:500;display:flex;align-items:center;justify-content:space-between;padding:0 110px}
.topbar .right{display:flex;align-items:center;gap:14px}
.topbar .sep{width:1px;height:18px;background:rgba(255,255,255,.6);margin:0 6px}
.topbar .social{width:12px;height:12px;background:#fff;border-radius:2px}
.header{height:86px;display:flex;align-items:center;justify-content:flex-end;padding:0 110px;position:relative;z-index:3}
.logo{position:absolute;left:108px;top:-4px;width:150px;height:150px;border-radius:50%;background:#fff;display:flex;flex-direction:column;align-items:center;justify-content:center}
.logo .ring{width:126px;height:126px;border-radius:50%;border:2px solid var(--blue);display:flex;flex-direction:column;align-items:center;justify-content:center}
.logo .name{color:var(--blue);font-weight:600;font-size:19px}
.logo .sub{color:var(--blue);font-weight:600;font-size:10px;margin-top:2px}
.nav{display:flex;gap:23px;font-size:15px;font-weight:500;align-items:center}
.nav svg{margin-left:2px}
.hero{position:absolute;top:124px;left:0;width:1200px;height:679px;background:linear-gradient(100deg,#1e2530 0%,#3c3a3a 35%,#5a4a3a 55%,#2c4660 80%,#1c3554 100%)}
.hero .photo{position:absolute;inset:0}
.hero .car{position:absolute;left:70px;top:310px;width:560px;height:270px;border-radius:120px 160px 60px 60px;background:radial-gradient(ellipse at center,#e8e8e8 0%,#bfc2c5 60%,rgba(180,180,180,0) 75%)}
.hero .welcome{position:absolute;left:111px;top:158px;color:#fff;font-size:25px;font-weight:500}
.hero h1{position:absolute;left:108px;top:195px;color:#fff;font-size:43px;font-weight:700}
.accent1{position:absolute;left:674px;top:35px;width:228px;height:298px;background:var(--blue);border-radius:8px 0 0 0}
.accent2{position:absolute;left:900px;top:334px;width:230px;height:298px;background:var(--blue);border-radius:0 0 8px 0}
.booking{position:absolute;left:695px;top:59px;width:415px;height:550px;background:#fff;border-radius:10px;padding:18px 35px 0}
.booking h2{text-align:center;color:var(--blue);font-size:27px;font-weight:600}
.booking .bar{width:150px;height:1px;background:var(--blue);margin:8px auto 14px}
.booking label{display:block;font-size:14px;font-weight:500;margin-bottom:6px}
.field{height:34px;border:1px solid #bbb;font-size:13px;color:#999;padding:0 12px;display:flex;align-items:center;justify-content:space-between;margin-bottom:18px}
.check{display:flex;align-items:center;gap:10px;font-size:14px;font-weight:500;margin:-2px 0 20px}
.check span.box{width:14px;height:14px;border:1px solid #999}
.row{display:flex;gap:25px}
.row>div{flex:1}
.btn-search{height:38px;background:var(--red);color:#fff;border-radius:19px;font-size:19px;display:flex;align-items:center;justify-content:center;gap:6px;box-shadow:0 3px 4px rgba(0,0,0,.25);margin-top:-2px}
.section-title{text-align:center;color:var(--blue);font-weight:800;font-size:39px}
.rule{width:400px;height:1px;background:var(--line);margin:0 auto}
.about{position:absolute;top:880px;left:0;width:1200px}
.about .lead{text-align:center;font-size:17px;font-weight:500;color:#333;margin:12px 0 28px}
.about .photo{position:absolute;left:113px;top:154px;width:630px;height:430px;background:linear-gradient(120deg,#d8dde3 0%,#9fb0c4 45%,#2a4a7a 75%,#1b2d4e 100%)}
.about .card{position:absolute;left:641px;top:195px;width:443px;height:300px;background:var(--red);color:#fff;padding:28px 20px}
.about .card::before{content:"";position:absolute;left:-50px;top:125px;border-style:solid;border-width:30px 50px 30px 0;border-color:transparent var(--red) transparent transparent}
.about .card h3{font-size:26px;font-weight:700;margin-bottom:10px}
.about .card p{font-size:14.5px;line-height:23px;margin-bottom:14px}
.arrow{position:absolute;top:515px;width:56px;height:56px;border-radius:50%;background:var(--blue);display:flex;align-items:center;justify-content:center}
.clients{position:absolute;top:1550px;left:0;width:1200px;height:480px;background:linear-gradient(90deg,#f6f6f7,#ececee 50%,#f4f4f6)}
.clients .section-title{margin-top:78px}
.clients .rule{margin-top:14px}
.quote{position:absolute;top:191px;font-size:130px;line-height:1;color:#c8c8cc;font-family:Georgia,serif;font-weight:700}
.clients p{width:800px;margin:50px auto 0;text-align:center;font-size:16.5px;line-height:26.5px;color:#333}
.clients .who{text-align:center;font-size:26px;font-weight:500;margin-top:20px}
.dots{display:flex;justify-content:center;gap:14px;margin-top:22px}
.dots span{width:21px;height:21px;border-radius:50%;background:#b8b4ef}
.dots span.on{background:var(--blue)}
.articles{position:absolute;top:2105px;left:0;width:1200px}
.articles .rule{margin-top:16px}
.cards{display:flex;gap:28px;margin:44px 0 0 110px}
.post{width:308px;height:376px;border:1px solid #777}
.post .img{height:198px}
.post .body{padding:16px 8px 0}
.post .date{font-size:14.5px;font-weight:500}
.post h4{color:var(--blue);font-size:18.5px;font-weight:600;line-height:25px;margin:10px 0 10px;text-align:justify}
.post p{font-size:14px;line-height:20px;color:#555}
.more{width:166px;height:38px;margin:40px auto 0;background:var(--red);color:#fff;border-radius:19px;font-size:19px;display:flex;align-items:center;justify-content:center;box-shadow:0 3px 4px rgba(0,0,0,.25)}
.footer{position:absolute;top:2760px;left:0;width:1200px;height:258px;background:radial-gradient(ellipse at 50% 80%,#2a2a2a,#0e0e0e 70%)}
.footer .flogo{width:120px;height:120px;border-radius:50%;border:2px solid #fff;margin:52px auto 0;display:flex;flex-direction:column;align-items:center;justify-content:center;color:#fff;font-weight:600}
.footer .flogo .n{font-size:17px}
.footer .flogo .s{font-size:9px;margin-top:2px}
.footer nav{display:flex;justify-content:center;gap:27px;color:#fff;font-size:19px;font-weight:500;margin-top:24px}
.bottom{position:absolute;top:3018px;left:0;width:1200px;height:41px;background:var(--blue);color:#fff;font-size:16px;display:flex;align-items:center;justify-content:center}
</style>
</head>
<body>
<div class="topbar">
  <span>Reserve Now And Get The Best Offer !!!</span>
  <div class="right">
    <svg width="11" height="14" viewBox="0 0 11 14"><path d="M5.5 0A5.5 5.5 0 0 0 0 5.5C0 9.5 5.5 14 5.5 14S11 9.5 11 5.5A5.5 5.5 0 0 0 5.5 0zm0 7.5a2 2 0 1 1 0-4 2 2 0 0 1 0 4z" fill="#fff"/></svg>
    <span>Valmora Coast</span><span class="sep"></span>
    <span class="social"></span><span class="social"></span><span class="social"></span><span class="social"></span><span class="social"></span>
  </div>
</div>

<header class="header">
  <div class="logo"><div class="ring"><span class="name">QUENMIRA</span><span class="sub">Vehicle Rental</span></div></div>
  <nav class="nav">
    <span>Home</span><span>Fleet</span><span>Promotions</span><span>Extras &amp; Services</span><span>About Us</span><span>Partners</span><span>Contact Us</span>
    <svg width="15" height="15" viewBox="0 0 15 15"><circle cx="6" cy="6" r="4.6" fill="none" stroke="#1a0fd6" stroke-width="2"/><path d="M9.5 9.5l4 4" stroke="#1a0fd6" stroke-width="2.2"/></svg>
  </nav>
</header>

<section class="hero">
  <div class="photo" role="img" aria-label="Evening view over a coastal town with terracotta roofs by the water"></div>
  <div class="car" role="img" aria-label="White compact SUV"></div>
  <div class="welcome">WELCOME TO</div>
  <h1>Quenmira Limitada</h1>
  <div class="accent1"></div><div class="accent2"></div>
  <form class="booking">
    <h2>Make a Reservation</h2><div class="bar"></div>
    <label>Pick up location</label>
    <div class="field">Please Choose...<svg width="11" height="7"><path d="M1 1l4.5 4.5L10 1" stroke="#555" fill="none" stroke-width="1.5"/></svg></div>
    <div class="check"><span class="box"></span>Pick up location same as return location</div>
    <label>Driver's age</label>
    <div class="field">Please Choose...<svg width="11" height="7"><path d="M1 1l4.5 4.5L10 1" stroke="#555" fill="none" stroke-width="1.5"/></svg></div>
    <label>Vehicle category</label>
    <div class="field">All<svg width="11" height="7"><path d="M1 1l4.5 4.5L10 1" stroke="#555" fill="none" stroke-width="1.5"/></svg></div>
    <div class="row"><div><label>Pick up date</label><div class="field">dd-mm-yyyy</div></div><div><label>Hour</label><div class="field">9:00</div></div></div>
    <div class="row"><div><label>Drop off date</label><div class="field">dd-mm-yyyy</div></div><div><label>Hour</label><div class="field">9:00</div></div></div>
    <div class="btn-search">Search <svg width="19" height="19" viewBox="0 0 15 15"><circle cx="6" cy="6" r="4.6" fill="none" stroke="#fff" stroke-width="2.2"/><path d="M9.5 9.5l4 4" stroke="#fff" stroke-width="2.6"/></svg></div>
  </form>
</section>

<section class="about">
  <h2 class="section-title">ABOUT US</h2>
  <p class="lead">WIDE RANGE OF LUXURY, SPORTS, AND HYBRID VEHICLES</p>
  <div class="rule"></div>
  <div class="photo" role="img" aria-label="Smiling driver in a blue car receiving the keys"></div>
  <div class="card">
    <h3>ABOUT CAR</h3>
    <p>Lorem ipsum dolor sit amet, consectetur adipiscing elit, sed do eiusmod tempor incididunt ut labore et dolore magna aliqua. Quis ipsum suspendisse ultrices gravida. Risus com modo viverra maecenas accumsan lacus vel facilisis.</p>
    <p>Lorem ipsum dolor sit amet, consectetur adipiscing elit, sed do eiusmod tempor incididunt ut labore et dolore magna aliqua.</p>
  </div>
  <div class="arrow" style="left:766px"><svg width="16" height="26"><path d="M13 2L3 13l10 11" stroke="#fff" stroke-width="3" fill="none"/></svg></div>
  <div class="arrow" style="left:853px"><svg width="16" height="26"><path d="M3 2l10 11L3 24" stroke="#fff" stroke-width="3" fill="none"/></svg></div>
</section>

<section class="clients">
  <h2 class="section-title">WHAT CLIENTS SAY ABOUT US?</h2>
  <div class="rule"></div>
  <span class="quote" style="left:108px">“</span>
  <span class="quote" style="left:1028px">”</span>
  <p>Sed ut perspiciatis unde omnis iste natus error sit voluptatem accusantium doloremque laudantium, totam rem aperiam, eaque ipsa quae ab illo inventore veritatis et quasi architecto beatae vitae dicta sunt explicabo. Nemo enim ipsam voluptatem quia voluptas sit aspernatur aut odit aut fugit, sed quia consequuntur magni dolores eos qui ratione voluptatem sequi nesciunt.</p>
  <div class="who">Rafael</div>
  <div class="dots"><span></span><span class="on"></span><span></span><span></span></div>
</section>

<section class="articles">
  <h2 class="section-title">ARTICLES &amp; TIPS</h2>
  <div class="rule"></div>
  <div class="cards">
    <article class="post"><div class="img" role="img" aria-label="Hand on a steering wheel" style="background:linear-gradient(135deg,#9fb08a,#4a4f55 60%,#1f2226)"></div><div class="body"><div class="date">APRIL 09, 2024</div><h4>Lorem ipsum dolor sit amet, con sectetur adipiscing</h4><p>Lorem ipsum dolor sit amet, con secte adipiscing elit, sed do eiusmod tempor incididunt ut labore et dolore</p></div></article>
    <article class="post"><div class="img" role="img" aria-label="White SUV driving on an open country road" style="background:linear-gradient(180deg,#a9b5bf,#c8cfd2 45%,#7a8a5a 60%,#6e6e6e 100%)"></div><div class="body"><div class="date">APRIL 09, 2024</div><h4>Lorem ipsum dolor sit amet, con sectetur adipiscing</h4><p>Lorem ipsum dolor sit amet, con secte adipiscing elit, sed do eiusmod tempor incididunt ut labore et dolore</p></div></article>
    <article class="post"><div class="img" role="img" aria-label="Row of parked cars in a lot" style="background:linear-gradient(120deg,#b03030,#8a8d90 35%,#a9aca8 70%,#8c7060)"></div><div class="body"><div class="date">APRIL 09, 2024</div><h4>Lorem ipsum dolor sit amet, con sectetur adipiscing</h4><p>Lorem ipsum dolor sit amet, con secte adipiscing elit, sed do eiusmod tempor incididunt ut labore et dolore</p></div></article>
  </div>
  <div class="more">View More</div>
</section>

<footer class="footer">
  <div class="flogo"><span class="n">QUENMIRA</span><span class="s">Vehicle Rental</span></div>
  <nav><span>Home</span><span>Fleet</span><span>Promotions</span><span>Extras &amp; Services</span><span>About Us</span><span>Partners</span><span>Contact Us</span></nav>
</footer>
<div class="bottom">© 2024 Quenmira Limitada. All Rights Reserved</div>
</body>
</html>
```